To design a brand identity that is simple and creative with 'Corvane' as the brand name, I like modern simple fonts like helvetica neue, I want to print both sides of the card, I am open to dark front and white back, but the design needs to transfer well to letter heads and email signatures, I am looking for sophisticated and elegant, but open minded about clever and off the wall, I do not do 'boring' Corvane Ventures is the mother company for a small group, specialising in Management & consulting, Software development and construction, we have a high level of integrity, we are transparent and accountable for what we do. my images are provided as a guide only, Im not expecting them to be just copied, Im looking for a creator and passionate thinker, who will put life into their work.

Target Market(s)

usually business minded people who are looking for something different in me, such as leadership, confidence and focus with thinking that is per haps a little outside the box..

Industry/Entity Type

Construction

Requirements
Must have
• clean, minmalistic
Nice to have
• custom logo
Should not have
• boring, traditional

```html
<!DOCTYPE html>
<html lang="en">
<head>
<meta charset="utf-8">
<title>Corvane — Business Card</title>
<link rel="stylesheet" href="https://fonts.googleapis.com/css2?family=Inter:wght@300;400&family=Cookie&display=swap">
<style>
  :root {
    --backdrop: #2f2b29;
    --card-light: #f1f1f2;
    --card-light-edge: #d9d9db;
    --card-dark: #4c4a4a;
    --card-dark-edge: #262626;
    --accent: #e4572e;
    --dot: #d6383a;
    --ink: #1e1e1e;
    --ink-soft: #3a3a3a;
    --ghost: #d3d3d5;
    --paper-white: #ffffff;
    --tagline-grey: #dcdcdc;
  }
  * { margin: 0; padding: 0; box-sizing: border-box; }
  html, body {
    width: 1000px; height: 1200px; overflow: hidden;
    background: var(--backdrop);
    font-family: "Inter", "Helvetica Neue", Arial, sans-serif;
  }
  .canvas { position: relative; width: 1000px; height: 1200px; }

  .card { position: absolute; width: 740px; height: 456px; overflow: hidden; }

  /* Front */
  .card--front {
    left: 136px; top: 75px;
    background: radial-gradient(ellipse at 40% 45%, var(--card-light) 35%, var(--card-light-edge) 100%);
  }
  .brand-lockup { position: absolute; left: 46px; top: 207px; }
  .brand-lockup__mark {
    position: absolute; left: 0; top: 9px;
    width: 44px; height: 44px; border-radius: 50%;
    background: var(--accent);
  }
  .brand-lockup__name {
    position: absolute; left: 56px; top: 0;
    font-weight: 300; font-size: 46px; line-height: 56px;
    color: var(--accent); letter-spacing: -0.5px; white-space: nowrap;
  }
  .brand-lockup__tagline {
    position: absolute; left: 94px; top: 54px;
    font-family: "Cookie", cursive; font-size: 21px; line-height: 22px;
    color: var(--ink); white-space: nowrap;
  }

  .divider-word {
    position: absolute; left: 382px; top: 230px;
    transform: translate(-50%, -50%) rotate(-90deg);
    font-weight: 300; font-size: 74px; line-height: 74px;
    color: var(--ghost); white-space: nowrap;
  }
  .service-line {
    position: absolute; left: 368px; top: 228px;
    transform: translate(-50%, -50%) rotate(-90deg);
    font-size: 15px; letter-spacing: 1px; color: var(--ink);
    white-space: nowrap;
  }
  .service-line .dot { color: var(--dot); }

  .contact { position: absolute; left: 454px; top: 136px; color: var(--ink-soft); }
  .contact__name { font-size: 26px; line-height: 32px; color: var(--accent); }
  .contact__role { font-size: 16px; line-height: 22px; color: var(--ink); margin-bottom: 6px; }
  .contact__row { font-size: 19px; line-height: 29px; font-weight: 300; color: var(--ink); }
  .contact__row .label { color: var(--accent); margin-right: 4px; }
  .contact__row--gap { margin-top: 12px; }

  /* Back */
  .card--back {
    left: 117px; top: 651px; height: 457px;
    background: radial-gradient(ellipse at 50% 40%, var(--card-dark) 0%, var(--card-dark-edge) 75%);
  }
  .back-lockup {
    position: absolute; left: 0; right: 0; top: 172px;
    display: flex; align-items: center; justify-content: center; gap: 22px;
  }
  .back-lockup__mark {
    width: 90px; height: 90px; border-radius: 50%;
    background: var(--accent);
  }
  .back-lockup__name {
    font-weight: 300; font-size: 88px; line-height: 100px;
    color: var(--paper-white); letter-spacing: -1px;
  }
  .back-services {
    position: absolute; left: 0; right: 0; top: 297px;
    text-align: center; font-size: 15px; letter-spacing: 1.5px;
    color: var(--tagline-grey);
  }
  .back-services .dot { color: var(--dot); margin: 0 6px; }
</style>
</head>
<body>
<main class="canvas">
  <section class="card card--front" aria-label="Card front">
    <div class="brand-lockup">
      <span class="brand-lockup__mark" aria-hidden="true"></span>
      <span class="brand-lockup__name">corvane</span>
      <span class="brand-lockup__tagline">... in the creation business</span>
    </div>

    <div class="divider-word" aria-hidden="true">corvane</div>
    <div class="service-line">management <span class="dot">•</span> software <span class="dot">•</span> construction</div>

    <div class="contact">
      <p class="contact__name">Mara Lindqvist</p>
      <p class="contact__role">client ambassador</p>
      <p class="contact__row"><span class="label">c.</span>+61 0400 555 019</p>
      <p class="contact__row"><span class="label">e.</span>info@corvane.com.au</p>
      <p class="contact__row contact__row--gap"><span class="label">a.</span>po box 418 perth 6000</p>
      <p class="contact__row"><span class="label">w.</span>www.corvane.com.au</p>
    </div>
  </section>

  <section class="card card--back" aria-label="Card back">
    <div class="back-lockup">
      <span class="back-lockup__mark" aria-hidden="true"></span>
      <span class="back-lockup__name">corvane.</span>
    </div>
    <p class="back-services">management<span class="dot">•</span>software<span class="dot">•</span>construction</p>
  </section>
</main>
</body>
</html>
```